FAIRWAY DEFENSE

I'm virtually ready to launch my site, but I have a number of edits and modifications that need to be implemented. More importantly, I'm always looking to improve my site, particularly now that I am making my proverbial "FIRST IMPRESSION." Thus, I'm willing to see if there is someone who can add creativity and perhaps improve what I already have, particularly on the All Important Front Page.

```html
<!DOCTYPE html>
<html lang="en">
<head>
<meta charset="utf-8">
<title>Fairway Defense – Legal Precision, Client Success</title>
<link href="https://fonts.googleapis.com/css2?family=Readex+Pro:wght@400;500;600;700&family=Inter:wght@400;500;600;700&display=swap" rel="stylesheet">
<style>
:root{
  --navy:#1b2e52;
  --navy-deep:#14233f;
  --navy-card:#22395e;
  --footer:#1f3663;
  --red:#b3141c;
  --red-dark:#8f0f16;
  --grey-bg:#f4f4f5;
  --ink:#14223d;
  --muted:#8a8f99;
  --line:#d7dae0;
  --white:#ffffff;
}
*{margin:0;padding:0;box-sizing:border-box}
html,body{width:1200px;height:4841px;overflow:hidden}
body{position:relative;background:var(--white);font-family:"Inter",sans-serif;color:var(--ink)}
.abs{position:absolute}
.head{font-family:"Readex Pro",sans-serif}
.eyebrow{font-size:12px;font-weight:500;color:var(--red);text-transform:uppercase;letter-spacing:.3px;border-bottom:1px solid var(--red);padding-bottom:2px}
.btn{position:absolute;background:var(--red);color:var(--white);font-weight:700;font-size:15px;display:flex;align-items:center;justify-content:center;gap:14px;border-radius:2px}
.btn svg{width:18px;height:18px}
.ph{position:absolute}

/* top bar */
.topbar{top:0;left:0;width:1200px;height:47px;background:var(--navy-deep);color:#d8dce6;font-size:13px}
.topbar span{position:absolute;top:15px}
.sq-social{position:absolute;top:17px;width:11px;height:11px;background:#aab2c4;border-radius:2px}

/* header */
.brand{display:flex;align-items:center;gap:10px;font-family:"Readex Pro",sans-serif;font-weight:600;color:var(--navy)}
.brand i{display:block;border-radius:50%;background:var(--red);border:3px solid var(--navy)}
.contact-mini{font-size:13px;line-height:22px}
.contact-mini b{font-weight:500;color:var(--ink)}
.contact-mini small{font-size:13px;color:var(--muted)}
.nav{top:154px;left:79px;width:986px;height:70px;background:var(--white);display:flex;align-items:center;padding-left:85px;gap:0;font-size:13px;color:#7a7f8a;z-index:3}
.nav a{width:110px;text-decoration:none;color:inherit}
.nav-call{top:154px;left:1065px;width:73px;height:70px;background:var(--navy);z-index:3;display:flex;align-items:center;justify-content:center}

/* hero */
.hero{top:154px;left:0;width:1200px;height:785px;background:linear-gradient(100deg,#1e2c4a 0%,#2f3d58 45%,#4a5366 70%,#303b52 100%)}
.hero-tag{top:447px;left:100px;width:266px;height:45px;background:var(--navy);border-left:4px solid var(--red);color:var(--white);font-weight:700;font-size:20px;padding:10px 0 0 20px}
.hero h1{top:518px;left:100px;font-size:58px;font-weight:700;color:var(--white);font-family:"Inter",sans-serif;letter-spacing:-.5px}
.hero-copy{top:608px;left:101px;width:520px;font-size:18px;line-height:27px;color:#eef0f4}

/* about */
.about-title{top:1095px;left:82px;font-size:42px;font-weight:500;line-height:53px;color:var(--ink)}
.about-sub{top:1226px;left:82px;font-size:23px;font-weight:400;color:var(--ink)}
.about-copy{top:1272px;left:82px;width:505px;font-size:12px;line-height:22px;color:var(--muted)}
.badge{top:1236px;left:819px;width:76px;height:76px;border-radius:50%;background:var(--white);display:flex;align-items:center;justify-content:center;box-shadow:0 4px 14px rgba(0,0,0,.12)}
.badge i{width:44px;height:44px;border-radius:50%;background:var(--red);border:3px solid var(--navy)}

/* services */
.services{top:1559px;left:0;width:1200px;height:650px;background:var(--grey-bg)}
.svc-card{position:absolute;top:1769px;width:318px;height:353px;border-radius:4px;overflow:hidden}
.svc-card h3{position:absolute;left:28px;top:230px;color:var(--white);font-family:"Readex Pro",sans-serif;font-weight:600;font-size:24px}
.svc-card h3::before{content:"";position:absolute;left:-8px;top:-2px;width:16px;height:16px;border-radius:50%;background:var(--red);z-index:-1}
.svc-arrow{position:absolute;left:28px;top:283px;width:48px;height:48px;border-radius:50%;background:rgba(255,255,255,.22);display:flex;align-items:center;justify-content:center}

/* experts */
.experts{top:2209px;left:0;width:1200px;height:385px;background:linear-gradient(90deg,#24385d 0%,#2c4066 50%,#34466a 100%)}
.exp-title{top:2312px;left:90px;font-size:41px;font-weight:600;line-height:54px;color:var(--white)}
.feat{position:absolute;top:2321px;width:233px;height:365px;background:var(--white);box-shadow:0 6px 24px rgba(20,35,63,.14);text-align:center}
.feat svg{position:absolute;top:34px;left:50%;margin-left:-26px;width:52px;height:52px}
.feat h4{position:absolute;top:103px;left:0;width:100%;font-family:"Readex Pro",sans-serif;font-weight:500;font-size:21px;color:var(--ink)}
.feat p{position:absolute;top:162px;left:22px;width:189px;font-size:12px;line-height:17.5px;color:var(--muted)}
.feat a{position:absolute;top:306px;left:0;width:100%;font-size:13px;font-weight:600;color:var(--navy);text-decoration:none}

/* why */
.why-title{top:2776px;left:0;width:1200px;text-align:center;font-size:40px;font-weight:600;color:var(--ink)}
.why-photo{top:2905px;left:432px;width:330px;height:330px;border-radius:50%;background:radial-gradient(circle at 50% 40%,#6c7c99 0%,#3c4e70 55%,#263a5e 100%)}
.why-item{position:absolute;width:220px}
.why-item h5{font-family:"Readex Pro",sans-serif;font-weight:400;font-size:20px;color:var(--navy);margin-bottom:8px}
.why-item p{font-size:12px;line-height:17px;color:var(--muted)}
.why-ic{position:absolute;width:80px;height:80px;border-radius:50%;background:var(--white);box-shadow:0 4px 18px rgba(0,0,0,.1);display:flex;align-items:center;justify-content:center}
.why-ic svg{width:32px;height:32px}

/* reviews */
.reviews{top:3333px;left:0;width:1200px;height:536px;background:var(--navy)}
.rev-title{top:3424px;left:0;width:1200px;text-align:center;font-size:40px;font-weight:600;color:var(--white)}
.rev-card{position:absolute;top:3548px;width:321px;height:216px;background:var(--navy-card);border-radius:3px;color:var(--white)}
.rev-card .q{position:absolute;top:-10px;left:50%;margin-left:-19px;font-family:Georgia,serif;font-size:70px;line-height:70px;color:var(--red);font-weight:700}
.rev-card p{position:absolute;top:30px;left:33px;width:264px;font-size:12.5px;line-height:19px}
.rev-card .av{position:absolute;top:137px;left:28px;width:48px;height:48px;border-radius:50%;background:linear-gradient(135deg,#e7d7c6,#c3a58a)}
.rev-card b{position:absolute;top:142px;left:95px;font-weight:500;font-size:15px}
.rev-card small{position:absolute;top:164px;left:95px;font-size:15px;color:#8c9ab3}
.dots{top:3789px;left:566px;display:flex;gap:6px;align-items:center}
.dots i{width:6px;height:6px;border-radius:50%;background:#8fa0c0;display:block}
.dots i.on{width:10px;height:10px;background:var(--red)}

/* contact */
.ct-title{top:3982px;left:101px;font-size:42px;font-weight:500;color:var(--ink)}
.ct-item{position:absolute;left:113px;display:flex;gap:22px}
.ct-item svg{width:44px;height:44px}
.ct-item b{display:block;font-size:13px;font-weight:600;margin-top:6px;color:var(--ink)}
.ct-item small{font-size:13px;color:var(--muted)}
.form{top:3976px;left:597px;width:494px;height:571px;background:var(--white);border-top:5px solid var(--navy);box-shadow:0 8px 30px rgba(20,35,63,.15);z-index:4}
.form h3{position:absolute;top:46px;left:37px;font-family:"Readex Pro",sans-serif;font-weight:500;font-size:25px;color:var(--ink)}
.form label{position:absolute;font-size:13px;font-weight:600;color:var(--ink)}
.field{position:absolute;border:1px solid var(--line);border-radius:14px;font-size:12px;color:#9aa0aa;padding:13px 0 0 24px;height:43px}
.field.area{border-radius:12px;height:121px}

/* footer */
.foot-info{position:absolute;top:4610px;display:flex;gap:12px;font-size:13px;line-height:19px;color:#e3e7ef}
.foot-info svg{width:28px;height:28px;flex:none;margin-top:4px}
.foot-nav{top:4695px;left:257px;width:753px;border-top:1px solid #5b6f97;padding-top:18px;display:flex;justify-content:space-around;font-size:14px;color:var(--white)}
.foot-soc{position:absolute;top:4793px;width:26px;height:26px;border:1px solid #9aa7c2;border-radius:2px}
</style>
</head>
<body>

<!-- top bar -->
<div class="abs topbar">
  <svg class="abs" style="left:76px;top:16px" width="14" height="14" viewBox="0 0 14 14"><circle cx="7" cy="7" r="6" fill="none" stroke="#b3141c" stroke-width="1.4"/><path d="M7 3.5V7l2.5 1.5" stroke="#b3141c" stroke-width="1.4" fill="none"/></svg>
  <span style="left:103px">Mon-Sat: 09am to 07:30pm</span>
  <svg class="abs" style="left:324px;top:17px" width="15" height="12" viewBox="0 0 15 12"><rect x=".7" y=".7" width="13.6" height="10.6" fill="none" stroke="#b3141c" stroke-width="1.3"/><path d="M1 1l6.5 5.5L14 1" fill="none" stroke="#b3141c" stroke-width="1.3"/></svg>
  <span style="left:348px">info@company.com</span>
  <span style="left:870px;color:#58627a">|</span>
  <span style="left:886px">Faqs</span>
  <span style="left:937px;color:#58627a">|</span>
  <span style="left:953px">Pricing</span>
  <span style="left:1019px;color:#58627a">|</span>
  <i class="sq-social" style="left:1036px"></i><i class="sq-social" style="left:1059px"></i><i class="sq-social" style="left:1093px"></i><i class="sq-social" style="left:1124px"></i>
</div>

<!-- header -->
<div class="abs brand" style="top:80px;left:98px;font-size:14px"><i style="width:40px;height:40px"></i>Fairway Defense</div>
<div class="abs contact-mini" style="top:74px;left:366px;display:flex;gap:16px">
  <svg width="30" height="30" viewBox="0 0 30 30"><path d="M15 4C8.4 4 4 8.3 4 13.6c0 3 1.5 5.6 4 7.3L7 26l5-2.8c1 .2 2 .3 3 .3 6.6 0 11-4.3 11-9.6S21.6 4 15 4z" fill="none" stroke="#14223d" stroke-width="1.8"/><circle cx="10.5" cy="14" r="1.3" fill="#14223d"/><circle cx="15" cy="14" r="1.3" fill="#14223d"/><circle cx="19.5" cy="14" r="1.3" fill="#14223d"/></svg>
  <div><b>+12-345-67-8900</b><br><small>Needhelp? Make a Call</small></div>
</div>
<div class="abs contact-mini" style="top:74px;left:663px;display:flex;gap:16px">
  <svg width="32" height="32" viewBox="0 0 32 32" fill="none" stroke="#14223d" stroke-width="1.6"><circle cx="16" cy="16" r="12"/><ellipse cx="16" cy="16" rx="5.5" ry="12"/><path d="M4 16h24M6 10h20M6 22h20"/></svg>
  <div><b>City, Country</b><br><small>123A Someplace</small></div>
</div>
<div class="btn" style="top:75px;left:958px;width:180px;height:49px;border-radius:3px;font-size:13px">Free Estimate
  <svg viewBox="0 0 20 20"><circle cx="10" cy="10" r="8.5" fill="none" stroke="#fff" stroke-width="1.6"/><path d="M8.5 6.5L12 10l-3.5 3.5" fill="none" stroke="#fff" stroke-width="1.6"/></svg>
</div>

<!-- hero -->
<div class="abs hero" role="img" aria-label="Photo of a smiling lawyer in a suit with colleagues at a meeting table"></div>
<nav class="abs nav"><a>Home</a><a>About Us</a><a>Services</a><a>Solutions</a><a style="width:90px">Team</a><a>Gallery</a><a>Contact Us</a></nav>
<div class="abs nav-call"><svg width="36" height="36" viewBox="0 0 24 24" fill="none" stroke="#fff" stroke-width="1.3"><path d="M6.6 3.5l2.6 3.7-1.6 2.3c1.2 2.6 3.2 4.6 5.9 5.9l2.3-1.6 3.7 2.6-1.2 3c-7.8 0-13.9-6.1-13.9-13.9z"/><path d="M14 4.5a6 6 0 0 1 5.5 5.5M14 1.5a9 9 0 0 1 8.5 8.5"/></svg></div>
<div class="abs hero-tag">We are leaders in</div>
<h1 class="abs" style="top:518px;left:100px;font-size:57px;font-weight:700;color:#fff">Legal Precision, Client Success</h1>
<p class="abs hero-copy">Lorem ipsum dolor sit amet, consectetur adipiscing elit, sed do eiusmod tempor incididunt ut labore et d</p>
<div class="btn" style="top:689px;left:100px;width:176px;height:51px">Read More</div>
<svg class="abs" style="top:840px;left:0" width="1200" height="110" viewBox="0 0 1200 110">
  <path d="M0 99 L0 80 Q500 55 1200 0 L1200 110 L0 110Z" fill="#fff"/>
  <path d="M0 88 Q220 60 700 50 Q320 64 0 99Z" fill="#b3141c"/>
</svg>

<!-- about -->
<span class="abs eyebrow" style="top:1063px;left:82px">Who we are</span>
<h2 class="abs head about-title">The team you can trust<br>to get the job done</h2>
<h3 class="abs head about-sub">Turning Challenges into Legal Triumphs</h3>
<p class="abs about-copy">Lorem ipsum dolor sit amet, consectetur adipiscing elit, sed do eiusmod tempor incididunt ut labore et dolore magna aliqua. Ut enim ad minim veniam, quis nos trud exercitation ullamco laboris nisi ut aliquip ex ea commodo consequat. Duis aute irure dolor in reprehenderit in voluptate velit esse cillum dolore eu fugiat nulla pariatur. Excepteur sint occaecat cupidatat non proident, sunt in culpa qui officia deserunt mollit anim id est laborum.</p>
<div class="btn" style="top:1431px;left:83px;width:154px;height:45px;font-size:14px">Contact us <svg viewBox="0 0 20 20"><path d="M3 10h13M11 5l5 5-5 5" fill="none" stroke="#fff" stroke-width="1.8"/></svg></div>
<div class="ph" style="top:1046px;left:616px;width:238px;height:426px;background:linear-gradient(160deg,#5b6d8c,#2c3d5e 60%,#3e4a62)" role="img" aria-label="Photo of a smiling lawyer shaking hands"></div>
<div class="ph" style="top:1078px;left:870px;width:238px;height:424px;background:linear-gradient(160deg,#4d6288,#27406a 55%,#1d3357)" role="img" aria-label="Photo of hands reviewing a document with a pen"></div>
<div class="abs badge"><i></i></div>

<!-- services -->
<div class="abs services"></div>
<span class="abs eyebrow" style="top:1619px;left:87px;font-size:11px">Our services</span>
<h2 class="abs head" style="top:1654px;left:87px;font-size:40px;font-weight:500;color:var(--ink)">Services We Provide</h2>
<span class="abs" style="top:1670px;left:943px;font-size:13px;color:var(--navy)">More Services</span>
<div class="abs" style="top:1659px;left:1075px;width:40px;height:39px;background:var(--red);display:flex;align-items:center;justify-content:center"><svg width="14" height="14" viewBox="0 0 14 14"><path d="M5 2l5 5-5 5" fill="none" stroke="#fff" stroke-width="2"/></svg></div>

<div class="svc-card" style="left:96px;background:linear-gradient(180deg,#5a4a3e 0%,#3a3a44 40%,#1f3a68 100%)" role="img" aria-label="Photo of a judge's gavel in a dim courtroom">
  <h3>Consultation</h3><div class="svc-arrow"><svg width="16" height="16" viewBox="0 0 16 16"><path d="M2 8h11M9 4l4 4-4 4" fill="none" stroke="#fff" stroke-width="1.6"/></svg></div></div>
<div class="svc-card" style="left:443px;background:linear-gradient(180deg,#8e96a6 0%,#4f5e7a 45%,#1f3a68 100%)" role="img" aria-label="Photo of a lawyer signing papers at a desk">
  <h3>Litigation</h3><div class="svc-arrow"><svg width="16" height="16" viewBox="0 0 16 16"><path d="M2 8h11M9 4l4 4-4 4" fill="none" stroke="#fff" stroke-width="1.6"/></svg></div></div>
<div class="svc-card" style="left:789px;background:linear-gradient(180deg,#6d8fbf 0%,#3f6199 45%,#1f3a68 100%)" role="img" aria-label="Photo of a hand touching digital law icons">
  <h3>Collection Claims</h3><div class="svc-arrow"><svg width="16" height="16" viewBox="0 0 16 16"><path d="M2 8h11M9 4l4 4-4 4" fill="none" stroke="#fff" stroke-width="1.6"/></svg></div></div>

<!-- experts -->
<div class="abs experts" role="img" aria-label="Faded photo of a legal team meeting in an office"></div>
<h2 class="abs head exp-title">Leading<br>Experts</h2>
<div class="btn" style="top:2481px;left:90px;width:152px;height:45px;font-size:14px">Contact us <svg viewBox="0 0 20 20"><path d="M3 10h13M11 5l5 5-5 5" fill="none" stroke="#fff" stroke-width="1.8"/></svg></div>

<div class="feat" style="left:353px">
  <svg viewBox="0 0 52 52" fill="none" stroke="#b3141c" stroke-width="2.6"><path d="M22 28V9a4 4 0 0 1 8 0v14l8 2c3 1 4 3 3 6l-3 11H22l-7-9c-2-2 0-5 3-4z"/><circle cx="26" cy="9" r="7" stroke-width="1.8"/></svg>
  <h4>Profesionalism</h4>
  <p>Lorem ipsum dolor sit amet, consectetur adipiscing elit, sed do eiusmod tem por incididunt ut labore et dolore magna aliqua. Ut enim ad minim veniam.</p>
  <a>Read More &nbsp;→</a>
</div>
<div class="feat" style="left:612px">
  <svg viewBox="0 0 52 52" fill="#b3141c"><rect x="4" y="34" width="6" height="14"/><rect x="13" y="26" width="6" height="22"/><circle cx="35" cy="10" r="5"/><path d="M28 18h14v14h-3v16h-8V32h-3z"/><path d="M6 26l10-10 5 5" fill="none" stroke="#b3141c" stroke-width="2.5"/></svg>
  <h4>Expertise</h4>
  <p>Lorem ipsum dolor sit amet, consectetur adipiscing elit, sed do eiusmod tem por incididunt ut labore et dolore magna aliqua. Ut enim ad minim veniam.</p>
  <a>Read More &nbsp;→</a>
</div>
<div class="feat" style="left:875px">
  <svg viewBox="0 0 52 52" fill="none" stroke="#b3141c" stroke-width="3"><circle cx="26" cy="16" r="8"/><path d="M10 42c0-8 7-13 16-13s16 5 16 13z"/><path d="M6 46h40"/></svg>
  <h4>Affordable</h4>
  <p>Lorem ipsum dolor sit amet, consectetur adipiscing elit, sed do eiusmod tem por incididunt ut labore et dolore magna aliqua. Ut enim ad minim veniam.</p>
  <a>Read More &nbsp;→</a>
</div>

<!-- why choose us -->
<span class="abs eyebrow" style="top:2739px;left:574px;font-size:11px">Why us</span>
<h2 class="abs head why-title">Why Choose Us</h2>
<div class="abs why-photo" role="img" aria-label="Photo of a confident lawyer in glasses with arms crossed"></div>

<div class="why-item" style="top:2910px;left:148px"><h5>Client Centric</h5><p>Lorem ipsum dolor sit amet, consectetur adipiscing elit</p></div>
<div class="why-item" style="top:3035px;left:116px"><h5>Free Consultation</h5><p>Lorem ipsum dolor sit amet, consectetur adipiscing elit</p></div>
<div class="why-item" style="top:3160px;left:132px"><h5>Attorney Letters</h5><p>Lorem ipsum dolor sit amet, consectetur adipiscing elit</p></div>
<div class="why-item" style="top:2910px;left:892px"><h5>Minimize Exposure</h5><p>Lorem ipsum dolor sit amet, consectetur adipiscing elit</p></div>
<div class="why-item" style="top:3035px;left:900px"><h5>Affordable</h5><p>Lorem ipsum dolor sit amet, consectetur adipiscing elit</p></div>
<div class="why-item" style="top:3160px;left:877px"><h5>Legal Experts</h5><p>Lorem ipsum dolor sit amet, consectetur adipiscing elit</p></div>

<div class="why-ic" style="top:2903px;left:354px"><svg viewBox="0 0 32 32" fill="none" stroke="#b3141c" stroke-width="2.2"><circle cx="16" cy="7" r="3"/><path d="M5 12l11 3 11-3M16 15v5l-5 9M16 20l5 9"/></svg></div>
<div class="why-ic" style="top:3029px;left:321px"><svg viewBox="0 0 32 32" fill="none" stroke="#b3141c" stroke-width="2.4" stroke-dasharray="3 3"><circle cx="16" cy="16" r="11"/></svg></div>
<div class="why-ic" style="top:3153px;left:352px"><svg viewBox="0 0 32 32" fill="none" stroke="#b3141c" stroke-width="2.4"><path d="M6 18a10 10 0 0 1 20 0v7H6z"/><path d="M6 21h20"/></svg></div>
<div class="why-ic" style="top:2903px;left:762px"><svg viewBox="0 0 32 32" fill="none" stroke="#b3141c" stroke-width="2"><circle cx="16" cy="16" r="12"/><circle cx="16" cy="16" r="7"/><circle cx="16" cy="16" r="3" fill="#b3141c"/></svg></div>
<div class="why-ic" style="top:3029px;left:796px"><svg viewBox="0 0 32 32" fill="none" stroke="#b3141c" stroke-width="2.4"><path d="M6 18a10 10 0 0 1 20 0v7H6z"/><path d="M12 20h14"/></svg></div>
<div class="why-ic" style="top:3153px;left:762px"><svg viewBox="0 0 32 32" fill="none" stroke="#b3141c" stroke-width="2.2"><rect x="4" y="4" width="7" height="7"/><rect x="21" y="4" width="7" height="7"/><rect x="4" y="21" width="7" height="7"/><rect x="21" y="21" width="7" height="7"/><path d="M11 7.5h10M11 24.5h10M7.5 11v10M24.5 11v10"/></svg></div>

<!-- reviews -->
<div class="abs reviews"></div>
<span class="abs eyebrow" style="top:3389px;left:552px;font-size:11px">Testimonials</span>
<h2 class="abs head rev-title">Client Reviews</h2>

<div class="rev-card" style="left:92px"><span class="q">”</span><p>Lorem ipsum dolor sit amet, consectetur adipiscing elit, sed do eiusmod tem por incididunt ut labore et dolore magna aliqua. Ut enim ad minim veniam, q uis nostrud exercitation ullamco laboris</p><i class="av"></i><b>Shaun B.</b><small>Australia</small></div>
<div class="rev-card" style="left:439px"><span class="q">”</span><p>Lorem ipsum dolor sit amet, consectetur adipiscing elit, sed do eiusmod tem por incididunt ut labore et dolore magna aliqua. Ut enim ad minim veniam, q uis nostrud exercitation ullamco laboris</p><i class="av"></i><b>Shaun B.</b><small>Australia</small></div>
<div class="rev-card" style="left:787px"><span class="q">”</span><p>Lorem ipsum dolor sit amet, consectetur adipiscing elit, sed do eiusmod tem por incididunt ut labore et dolore magna aliqua. Ut enim ad minim veniam, q uis nostrud exercitation ullamco laboris</p><i class="av"></i><b>Shaun B.</b><small>Australia</small></div>
<div class="abs dots"><i></i><i></i><i class="on"></i><i></i><i></i></div>

<!-- footer shape -->
<svg class="abs" style="top:4320px;left:0" width="1200" height="521" viewBox="0 0 1200 521">
  <path d="M0 170 L1200 75 L1200 521 L0 521Z" fill="#1f3663"/>
  <path d="M1091 18 L1200 22 L1200 56 L1091 52Z" fill="#b3141c"/>
  <path d="M500 76 Q560 70 600 68 L600 72 Q540 78 500 80Z" fill="#b3141c"/>
</svg>

<!-- contact -->
<h2 class="abs head ct-title">Contact Us <span style="font-weight:400">Today</span></h2>
<div class="ct-item" style="top:4055px"><svg viewBox="0 0 44 44" fill="none" stroke="#b3141c" stroke-width="1.6"><path d="M22 30s-8-8-8-14a8 8 0 0 1 16 0c0 6-8 14-8 14z"/><circle cx="22" cy="16" r="3"/><path d="M12 28l-6 10h32l-6-10"/></svg><div><b>HEAD OFFICE</b><small>21 Lorem Ipsum, ABC 123</small></div></div>
<div class="ct-item" style="top:4128px"><svg viewBox="0 0 44 44" fill="none" stroke="#b3141c" stroke-width="1.6"><rect x="6" y="12" width="32" height="22"/><path d="M6 12l16 12 16-12M6 34l12-10M38 34l-12-10"/></svg><div><b>EMAIL ADDRESS</b><small>21 Lorem Ipsum, ABC 123</small></div></div>
<div class="ct-item" style="top:4196px"><svg viewBox="0 0 44 44" fill="none" stroke="#b3141c" stroke-width="1.6"><rect x="12" y="6" width="18" height="32" rx="3"/><path d="M19 33h4M34 16a6 6 0 0 1 0 10M37 12a10 10 0 0 1 0 18"/></svg><div><b>CALL US NOW</b><small>21 Lorem Ipsum, ABC 123</small></div></div>

<form class="abs form">
  <h3>Send Us A Message</h3>
  <label style="top:120px;left:37px">First Name</label>
  <label style="top:120px;left:251px">Last Name</label>
  <div class="field" style="top:132px;left:37px;width:200px">John</div>
  <div class="field" style="top:132px;left:252px;width:197px">Doe</div>
  <label style="top:206px;left:37px">Email</label>
  <div class="field" style="top:220px;left:37px;width:416px">info@company.com</div>
  <label style="top:294px;left:37px">Message</label>
  <div class="field area" style="top:309px;left:37px;width:416px">Type Your Message</div>
  <div class="btn" style="top:470px;left:38px;width:158px;height:45px;font-size:14px">Contact us <svg viewBox="0 0 20 20"><path d="M3 10h13M11 5l5 5-5 5" fill="none" stroke="#fff" stroke-width="1.8"/></svg></div>
</form>

<!-- footer -->
<div class="abs brand" style="top:4600px;left:152px;flex-direction:column;gap:6px;color:#fff;font-size:13px"><i style="width:70px;height:70px;border-color:#fff"></i>Fairway Defense</div>
<div class="abs" style="top:4598px;left:411px;width:1px;height:58px;background:#5b6f97"></div>
<div class="foot-info" style="left:432px"><svg viewBox="0 0 28 28" fill="none" stroke="#fff" stroke-width="1.5"><circle cx="14" cy="14" r="11"/><ellipse cx="14" cy="14" rx="5" ry="11"/><path d="M3 14h22"/></svg><div>123, Building Name, Street<br>City, State XY 123456</div></div>
<div class="abs" style="top:4608px;left:673px;width:1px;height:40px;background:#5b6f97"></div>
<div class="foot-info" style="left:688px"><svg viewBox="0 0 28 28" fill="none" stroke="#fff" stroke-width="1.5"><rect x="6" y="3" width="13" height="22" rx="2"/><path d="M22 10a4 4 0 0 1 0 8"/></svg><div>PHONE<br>(123) 456 7890</div></div>
<div class="abs" style="top:4608px;left:852px;width:1px;height:40px;background:#5b6f97"></div>
<div class="foot-info" style="left:866px"><svg viewBox="0 0 28 28" fill="none" stroke="#fff" stroke-width="1.5"><rect x="3" y="7" width="22" height="15"/><path d="M3 7l11 8 11-8"/></svg><div>EMAIL<br>info@company.com</div></div>

<div class="abs foot-nav"><span>HOME</span><span>SERVICES</span><span>ABOUT US</span><span>TESTIMONIALS</span><span>BLOG</span><span>CONTACT US</span></div>
<span class="abs" style="top:4796px;left:148px;font-size:11px;color:#fff">Fairway Defense</span>
<i class="foot-soc" style="left:935px"></i><i class="foot-soc" style="left:967px"></i><i class="foot-soc" style="left:999px"></i><i class="foot-soc" style="left:1031px"></i>

</body>
</html>
```